Wealth Education Business Needs Sharp Business Card Design

We need a business card design for a recently launched investor education business called Harbor Crest.

The final design should promote security, empowerment, self improvement and financial gain. The card will ideally promote the stature of the business.

For more information and colours please visit harborcrest.com.au

Target Market(s)

Corporate executives and high net worth individuals

Industry/Entity Type

Education

Contact Information for Business Card

```html
<!DOCTYPE html>
<html lang="en">
<head>
<meta charset="utf-8">
<title>Harbor Crest Business Card</title>
<link rel="stylesheet" href="https://fonts.googleapis.com/css2?family=Lato:wght@400;700&display=swap">
<style>
  :root {
    --backdrop: #e4e4e4;
    --card-white: #ffffff;
    --ink: #2e2e2e;
    --brand-teal: #12898a;
    --band-blue: #4c64a5;
    --band-teal: #13908f;
    --band-green: #5f9b4c;
    --back-teal: #0f9c9d;
    --back-teal-deep: #0a8686;
    --wordmark-dark: #383838;
  }
  html, body {
    margin: 0;
    padding: 0;
    width: 1200px;
    height: 720px;
    overflow: hidden;
    background: var(--backdrop);
    font-family: "Lato", sans-serif;
  }
  .stage {
    position: relative;
    width: 1200px;
    height: 720px;
  }
  .card {
    position: absolute;
    top: 240px;
    width: 420px;
    height: 240px;
    border-radius: 14px;
    overflow: hidden;
  }
  .card-front {
    left: 148px;
    background: var(--card-white);
  }
  .card-back {
    left: 633px;
    background: linear-gradient(135deg, var(--back-teal), var(--back-teal-deep));
    display: flex;
    align-items: center;
    justify-content: center;
  }
  .front-decor {
    position: absolute;
    left: 0;
    right: 0;
    bottom: 0;
    height: 72px;
    background: linear-gradient(100deg, var(--band-blue) 0%, var(--band-teal) 50%, var(--band-green) 100%);
  }
  .front-wordmark {
    position: absolute;
    left: 46px;
    top: 32px;
    display: flex;
    align-items: center;
    gap: 10px;
    font-size: 19px;
    font-weight: 400;
    letter-spacing: 3px;
    color: var(--ink);
  }
  .wordmark-dot {
    width: 12px;
    height: 12px;
    background: var(--brand-teal);
  }
  .holder {
    position: absolute;
    right: 20px;
    top: 16px;
    text-align: right;
  }
  .holder-name {
    font-size: 17px;
    font-weight: 700;
    color: var(--brand-teal);
    line-height: 20px;
  }
  .holder-role {
    font-size: 11px;
    font-weight: 700;
    color: var(--ink);
    line-height: 16px;
  }
  .contact-list {
    position: absolute;
    right: 20px;
    top: 64px;
    margin: 0;
    padding: 0;
    list-style: none;
    text-align: right;
    font-size: 12px;
    color: var(--ink);
  }
  .contact-list li {
    display: flex;
    justify-content: flex-end;
    align-items: center;
    gap: 5px;
    line-height: 14.5px;
  }
  .contact-list .address-line {
    margin-top: 7px;
  }
  .contact-list .address-cont {
    padding-right: 17px;
  }
  .contact-icon {
    width: 12px;
    height: 12px;
    flex: none;
  }
  .back-wordmark {
    display: flex;
    align-items: center;
    gap: 16px;
    font-size: 34px;
    font-weight: 400;
    letter-spacing: 7px;
    color: var(--wordmark-dark);
  }
  .back-wordmark .wordmark-dot {
    width: 18px;
    height: 18px;
    background: var(--wordmark-dark);
  }
</style>
</head>
<body>
<main class="stage">
  <section class="card card-front" aria-label="Business card front">
    <div class="front-decor" role="img" aria-label="Decorative flowing bands in blue, teal and green"></div>
    <div class="front-wordmark"><span class="wordmark-dot"></span>HARBOR CREST</div>
    <div class="holder">
      <div class="holder-name">Liam Carter</div>
      <div class="holder-role">Director</div>
    </div>
    <ul class="contact-list">
      <li>1300 555 014
        <svg class="contact-icon" viewBox="0 0 12 12"><path d="M2,4 C2,2 10,2 10,4 L8.5,5 L7.5,3.8 L4.5,3.8 L3.5,5 Z M3,6 L9,6 L10,10 L2,10 Z" fill="var(--brand-teal)"/></svg>
      </li>
      <li>+613 5550 2817
        <svg class="contact-icon" viewBox="0 0 12 12"><rect x="3.5" y="1" width="5" height="10" rx="1" fill="none" stroke="var(--brand-teal)" stroke-width="1.2"/></svg>
      </li>
      <li>support@harborcrest.com.au
        <svg class="contact-icon" viewBox="0 0 12 12"><rect x="1" y="2.5" width="10" height="7" fill="var(--brand-teal)"/><path d="M1,2.5 L6,6.5 L11,2.5" fill="none" stroke="#fff" stroke-width="1"/></svg>
      </li>
      <li>www.harborcrest.com.au
        <svg class="contact-icon" viewBox="0 0 12 12"><circle cx="6" cy="6" r="5" fill="none" stroke="var(--brand-teal)" stroke-width="1.1"/><ellipse cx="6" cy="6" rx="2.2" ry="5" fill="none" stroke="var(--brand-teal)" stroke-width="0.9"/><path d="M1,6 L11,6" stroke="var(--brand-teal)" stroke-width="0.9"/></svg>
      </li>
      <li class="address-line">Level 2, 47 Dockside Street
        <svg class="contact-icon" viewBox="0 0 12 12"><path d="M6,1 L11.5,6 L10,6 L10,11 L7.3,11 L7.3,7.5 L4.7,7.5 L4.7,11 L2,11 L2,6 L0.5,6 Z" fill="var(--brand-teal)"/></svg>
      </li>
      <li class="address-cont">Melbourne VIC 3000</li>
    </ul>
  </section>

  <section class="card card-back" aria-label="Business card back">
    <div class="back-wordmark"><span class="wordmark-dot"></span>HARBOR CREST</div>
  </section>
</main>
</body>
</html>
```